Business Card for a mobile physiotherapy company

I need a layout for a business card for a mobile physiotherapy company.
Slogan is "Mobile Physiotherapy - Your Road To Recovery"
Phone number is 867-555-0142
Email VardenTherapy@postnest.ca (subject to change with website)
Website www.VardenTherapy.ca
My name and credentials: Luke Varden Luke Varden, BSc(kin), MPT, CAFCI, IMS
Information maybe included: Direct Billing, Services including Physiotherapy, IMS, acupuncture
Maybe include facebook and instagram logos
One side with the logo clean and sharp
Other side with details, try not to look too busy, keep everything concise

```html
<!DOCTYPE html>
<html lang="en">
<head>
<meta charset="utf-8">
<title>Varden Therapy – Business Card</title>
<link rel="stylesheet" href="https://fonts.googleapis.com/css2?family=Carlito:wght@400;700&display=swap">
<style>
  :root {
    --stage: #3b3c3e;
    --navy: #264777;
    --navy-deep: #1f3d68;
    --green: #17614f;
    --paper: #ffffff;
    --card-w: 560px;
    --card-h: 320px;
  }
  * { margin: 0; padding: 0; box-sizing: border-box; }
  html, body {
    width: 1200px; height: 900px; overflow: hidden;
    background: var(--stage);
    font-family: "Carlito", "Calibri", sans-serif;
  }
  .stage {
    width: 1200px; height: 900px;
    display: flex; flex-direction: column; align-items: center; justify-content: center;
    gap: 70px;
  }
  .card {
    position: relative;
    width: var(--card-w); height: var(--card-h);
    overflow: hidden;
    box-shadow: 0 10px 30px rgba(0,0,0,.35);
  }

  /* Details side */
  .card--details { background: var(--paper); }
  .details-band { position: absolute; inset: 0; width: 100%; height: 100%; }
  .brand-mark {
    position: absolute; left: 34px; top: 34px;
    display: flex; align-items: center; gap: 10px;
  }
  .brand-square { width: 18px; height: 18px; background: var(--navy); }
  .brand-name {
    font-weight: 700; font-size: 26px; letter-spacing: 2px;
    color: var(--navy); text-transform: uppercase;
  }
  .contact-list {
    position: absolute; left: 34px; bottom: 30px;
    list-style: none; color: var(--paper); font-size: 15px; line-height: 1.55;
  }
  .contact-list li { display: flex; align-items: center; gap: 9px; }
  .contact-list svg { width: 11px; height: 11px; fill: var(--paper); flex: none; }
  .practitioner {
    position: absolute; right: 30px; top: 92px; text-align: right;
  }
  .practitioner-name {
    color: var(--navy); font-size: 27px; line-height: 1.12; font-weight: 400;
  }
  .practitioner-services {
    margin-top: 6px; color: var(--green); font-size: 17px; line-height: 1.2;
  }

  /* Brand side */
  .card--brand {
    background: linear-gradient(160deg, #2b4f82 0%, var(--navy-deep) 100%);
    display: flex; flex-direction: column; align-items: center; justify-content: center;
    gap: 18px;
  }
  .card--brand .brand-square { background: var(--paper); width: 22px; height: 22px; }
  .card--brand .brand-name { color: var(--paper); font-size: 40px; letter-spacing: 4px; }
  .card--brand .brand-mark { position: static; gap: 14px; }
  .slogan { color: var(--paper); font-size: 17px; }
</style>
</head>
<body>
<main class="stage">
  <section class="card card--details" aria-label="Card details side">
    <svg class="details-band" viewBox="0 0 560 320" preserveAspectRatio="none" aria-hidden="true">
      <polygon points="0,156 240,156 360,320 0,320" fill="var(--navy)"/>
    </svg>
    <div class="brand-mark">
      <span class="brand-square"></span>
      <span class="brand-name">Varden Therapy</span>
    </div>
    <ul class="contact-list">
      <li><svg viewBox="0 0 24 24"><path d="M6.6 10.8a15 15 0 0 0 6.6 6.6l2.2-2.2a1 1 0 0 1 1-.25 11.4 11.4 0 0 0 3.6.57 1 1 0 0 1 1 1V20a1 1 0 0 1-1 1A17 17 0 0 1 3 4a1 1 0 0 1 1-1h3.5a1 1 0 0 1 1 1c0 1.25.2 2.45.57 3.57a1 1 0 0 1-.25 1z"/></svg>867-555-0142</li>
      <li><svg viewBox="0 0 24 24"><path d="M2 5h20v14H2zm2 2v.5l8 5 8-5V7zm0 2.8V17h16V9.8l-8 5z"/></svg>VardenTherapy@postnest.ca</li>
      <li><svg viewBox="0 0 24 24"><circle cx="12" cy="12" r="10"/></svg>www.VardenTherapy.ca</li>
    </ul>
    <div class="practitioner">
      <h1 class="practitioner-name">Luke Varden, BSc(kin),<br>MPT, CAFCI, IMS</h1>
      <p class="practitioner-services">Direct Billing, Services including<br>Physiotherapy, IMS, acupuncture</p>
    </div>
  </section>

  <section class="card card--brand" aria-label="Card brand side">
    <div class="brand-mark">
      <span class="brand-square"></span>
      <span class="brand-name">Varden Therapy</span>
    </div>
    <p class="slogan">Mobile Physiotherapy - Your Road To Recovery</p>
  </section>
</main>
</body>
</html>
```